Brightway Haul & Upkeep Services, are a company that offers a 'one stop shop' pre-move clean up a

I have already selected a logo which I would like on the front of the business cards along with phone numbers, web address and email which are:
0487650392
www.brightwayhaul.com.au
brightwayhaulandupkeep@mailbox.example

On the back of the card I would like to list some of the types of service we offer (clean - move - repairs/maintenance) which are:
CLEAN - windows, gutters, solar panels, driveways/paths, carpets.
MOVE - Small/medium size house/office moves, large item pick-up & delivery, yard clean-up and removal.
General maintenance and repairs.

I would like the blue logo on a gray background.

Thanks

```html
<!DOCTYPE html>
<html lang="en">
<head>
<meta charset="utf-8">
<title>Brightway Haul &amp; Upkeep Services — Business Card</title>
<link rel="stylesheet" href="https://fonts.googleapis.com/css2?family=Ubuntu:wght@500;700&family=Open+Sans:wght@400;600;700&display=swap">
<style>
  :root {
    --page: #e7e4df;
    --card-grey: #adadad;
    --brand-blue: #1e6db7;
    --sky-blue: #7dbde9;
    --ink: #2a2a2a;
    --white: #ffffff;
  }
  * { margin: 0; padding: 0; box-sizing: border-box; }
  html, body {
    width: 1200px; height: 1083px; overflow: hidden;
    background: var(--page);
  }
  .canvas { position: relative; width: 1200px; height: 1083px; }

  .card {
    position: absolute;
    width: 833px; height: 475px;
    background: var(--card-grey);
    overflow: hidden;
    box-shadow: 0 2px 6px rgba(0,0,0,0.25);
  }
  .card--front { left: 45px; top: 37px; }
  .card--back  { left: 313px; top: 548px; }

  .brand-name {
    position: absolute;
    font-family: "Ubuntu", sans-serif;
    font-weight: 700;
    color: var(--brand-blue);
    font-size: 50px;
    line-height: 1.12;
    white-space: nowrap;
  }
  .card--front .brand-name { left: 62px; top: 118px; }
  .card--back .brand-name { left: 0; right: 0; top: 160px; text-align: center; }

  .contact {
    position: absolute; left: 60px; top: 288px;
    font-family: "Open Sans", sans-serif;
    font-size: 21px; color: var(--ink);
    list-style: none;
  }
  .contact li { display: flex; align-items: center; height: 34px; }
  .contact svg { width: 18px; height: 18px; margin-right: 9px; }

  .accent-band {
    position: absolute; left: 0; right: 0; bottom: 0; height: 78px;
    background: linear-gradient(to right, var(--sky-blue) 0%, var(--brand-blue) 55%, var(--brand-blue) 100%);
  }

  .website {
    position: absolute; right: 34px; top: 428px;
    font-family: "Open Sans", sans-serif;
    font-size: 21px; letter-spacing: 0.5px;
    color: var(--white);
  }

  .services-title {
    position: absolute; left: 0; right: 0; top: 310px;
    text-align: center;
    font-family: "Open Sans", sans-serif;
    font-weight: 700; font-size: 33px; letter-spacing: 3px;
    color: var(--brand-blue);
  }
  .services-list {
    position: absolute; left: 0; right: 0; top: 372px;
    text-align: center;
    font-family: "Open Sans", sans-serif;
    font-weight: 600; font-size: 25px; color: var(--ink);
    line-height: 42px;
  }
  .services-list .item { margin: 0 10px; }
  .services-list .item::before {
    content: "\2022"; color: var(--brand-blue); margin-right: 8px;
  }
</style>
</head>
<body>
<main class="canvas">

  <section class="card card--front" aria-label="Business card front">
    <div class="brand-name">Brightway Haul<br>&amp; Upkeep Services</div>

    <ul class="contact">
      <li>
        <svg viewBox="0 0 20 20" aria-hidden="true">
          <circle cx="10" cy="10" r="8.5" fill="none" stroke="var(--brand-blue)" stroke-width="1.6"/>
          <path d="M7 5.5 l2 2.2 -1.2 1.3 c0.8 1.5 1.7 2.4 3.2 3.2 l1.3-1.2 2.2 2 -1.4 1.6 c-3.5-0.4-6.9-3.8-7.3-7.3z" fill="var(--brand-blue)"/>
        </svg>
        0487650392
      </li>
      <li>
        <svg viewBox="0 0 20 20" aria-hidden="true">
          <rect x="1.5" y="4.5" width="17" height="12" rx="1.5" fill="var(--brand-blue)"/>
          <path d="M2.5 6 L10 11.5 L17.5 6" fill="none" stroke="var(--white)" stroke-width="1.5"/>
        </svg>
        brightwayhaulandupkeep@mailbox.example
      </li>
    </ul>

    <div class="accent-band" role="img" aria-label="Decorative blue wave band along the bottom of the card"></div>

    <div class="website">www.brightwayhaul.com.au</div>
  </section>

  <section class="card card--back" aria-label="Business card back">
    <div class="brand-name">Brightway Haul<br>&amp; Upkeep Services</div>

    <h2 class="services-title">Services we offer</h2>
    <div class="services-list">
      <div><span class="item">Clean</span><span class="item">Move</span></div>
      <div><span class="item">General Maintenance And Repairs.</span></div>
    </div>
  </section>

</main>
</body>
</html>
```